Modern Business Card for Larkwell 2018

Our company assumes the best about people. We are creating an online community of entrepreneurs and business leaders who struggle with marketing their business online.

This business card should POP! We recently got a new logo and are launching a new website next month, so our business cards should make a statement that feels:
-Fresh
-Smart
-Trustworthy
-Fun

Target Market(s)

small business owners, entrepreneurs

Industry/Entity Type

Digital Marketing

Contact Information for Business Card

Dimensions: 3.5" x 2"

Font styles to use
Sans Serif

Colors
f37122
ffffff

Requirements
Must have
• We need a business card with a modern, bold design. We will use one side of the card as a lead-generation offer, so text on one side will need to fit up to 140 characters. The business card should stick to our core colors (orange, black, and white).
Nice to have
• We think a vertical "portrait" design could be interesting.
Should not have
• Should not look like a traditional business card. The round icon should stand out from a distance.

```html
<!DOCTYPE html>
<html lang="en">
<head>
<meta charset="utf-8">
<title>Larkwell Business Card</title>
<link rel="stylesheet" href="https://fonts.googleapis.com/css2?family=Roboto:wght@400;500;700;900&family=Lobster&display=swap">
<style>
  :root {
    --orange: #f37122;
    --orange-deep: #f26a24;
    --white: #ffffff;
    --paper: #f4f4f4;
    --ink: #111111;
    --rule: #8a8a8a;
    --backdrop: #e9e6e2;
  }
  * { box-sizing: border-box; margin: 0; padding: 0; }
  html, body {
    width: 1200px; height: 960px; overflow: hidden;
    background: var(--backdrop);
    font-family: "Roboto", Arial, sans-serif;
  }
  .canvas { position: relative; width: 1200px; height: 960px; }

  .card {
    position: absolute;
    width: 600px; height: 342px;
    border-radius: 20px;
    overflow: hidden;
    box-shadow: 0 2px 6px rgba(0,0,0,0.18);
  }

  /* Front */
  .card-front { left: 314px; top: 113px; background: var(--paper); }
  .brand-front {
    position: absolute; left: 0; right: 0; top: 66px;
    display: flex; align-items: center; justify-content: center; gap: 16px;
  }
  .brand-dot { width: 78px; height: 78px; border-radius: 50%; background: var(--orange); }
  .brand-name-front {
    font-weight: 900; font-size: 40px; letter-spacing: 1px;
    color: var(--orange); text-transform: uppercase;
  }
  .name-band {
    position: absolute; left: 0; right: 0; top: 201px; height: 104px;
    background: var(--orange);
    border-top: 3px solid var(--rule);
    border-bottom: 3px solid var(--rule);
    text-align: center; color: var(--ink);
  }
  .person-name {
    font-family: "Lobster", "Brush Script MT", cursive;
    font-size: 38px; line-height: 1; margin-top: 14px; letter-spacing: 0.5px;
  }
  .person-role { font-size: 15px; font-weight: 500; margin-top: 7px; letter-spacing: 0.3px; }
  .person-email { font-size: 14px; margin-top: 3px; }

  /* Back */
  .card-back { left: 311px; top: 473px; background: var(--orange-deep); color: var(--white); }
  .brand-back {
    position: absolute; left: 30px; width: 260px; top: 100px; text-align: center;
  }
  .brand-name-back { font-weight: 900; font-size: 38px; letter-spacing: 1.5px; line-height: 1; text-transform: uppercase; }
  .brand-tagline { font-size: 11px; font-weight: 700; letter-spacing: 1.2px; margin-top: 8px; text-transform: uppercase; }
  .divider {
    position: absolute; left: 297px; top: 24px; width: 1px; height: 166px;
    background: rgba(255,255,255,0.75);
  }
  .offer { position: absolute; left: 323px; top: 28px; width: 260px; }
  .offer-headline { font-weight: 700; font-size: 18px; line-height: 21px; text-transform: uppercase; }
  .offer-body { font-size: 15px; line-height: 19px; margin-top: 7px; }
  .offer-url { font-weight: 700; font-size: 19px; margin-top: 8px; }
  .notes {
    position: absolute; left: 20px; top: 216px; width: 557px; height: 102px;
    background: var(--white); border-radius: 20px;
  }
  .notes-line { position: absolute; left: 24px; right: 28px; height: 1px; background: var(--ink); }
  .notes-line.first { top: 31px; }
  .notes-line.second { top: 71px; }
</style>
</head>
<body>
<main class="canvas">
  <section class="card card-front" aria-label="Card front">
    <div class="brand-front">
      <span class="brand-dot"></span>
      <span class="brand-name-front">Larkwell</span>
    </div>
    <div class="name-band">
      <p class="person-name">DANA WHITFIELD</p>
      <p class="person-role">STORY MARKETING COACH</p>
      <p class="person-email">dana@larkwellnow.com</p>
    </div>
  </section>

  <section class="card card-back" aria-label="Card back">
    <div class="brand-back">
      <p class="brand-name-back">Larkwell</p>
      <p class="brand-tagline">Tell stories that inspire action</p>
    </div>
    <div class="divider"></div>
    <div class="offer">
      <p class="offer-headline">Reach more people.<br>Make more money.<br>Create more impact.</p>
      <p class="offer-body">Get your free Larkwell<br>Starter Package and our<br>marketing guide today at</p>
      <p class="offer-url">Larkwellnow.com/start</p>
    </div>
    <div class="notes">
      <span class="notes-line first"></span>
      <span class="notes-line second"></span>
    </div>
  </section>
</main>
</body>
</html>
```